VELMOR Website Design

We need a website designed for our company VELMOR. We are a luxury lifestyle club that will provide benefits and services for our members. The site should be clean & sleek, preferably using black and white (or darker colors). (example sites: stravenhall.example, plinth.example)

Here is a link of a sample page I did using wix. (https://dunmere7.sitehostly.example/mysite) This can be used to get a general idea.

Target Market(s)

Upper Middle Class in the United States

Number of Pages Required

5+ page

Font styles to use
Sans Serif
Other font styles liked:
• Arial (or other similar fonts)

Requirements
Must have
• A clean design that is eye-catching and speaks to our company.
Nice to have
• Ideas for copy.

```html
<!DOCTYPE html>
<html lang="en">
<head>
<meta charset="utf-8">
<title>VELMOR — A Members Only Lifestyle Club</title>
<link rel="stylesheet" href="https://fonts.googleapis.com/css2?family=Catamaran:wght@600;700;800&family=Open+Sans:wght@400;600&family=Encode+Sans+Condensed:wght@300;400&display=swap">
<style>
:root{
  --ink:#0d0d0d;
  --paper:#ffffff;
  --dark:#111111;
  --dark-2:#1c1c1c;
  --muted:#8a8a8a;
  --faint:#4a4a4a;
  --line:#2a2a2a;
}
*{margin:0;padding:0;box-sizing:border-box}
html,body{width:1200px;height:2894px;overflow:hidden}
body{position:relative;background:var(--paper);color:var(--ink);font-family:"Open Sans",Arial,sans-serif}
.abs{position:absolute}
.center{left:0;width:1200px;text-align:center}

/* hero */
.hero{left:0;top:0;width:1200px;height:698px;
  background:linear-gradient(180deg,#1a1a1a 0%,#2b2b2b 35%,#3a3a3a 60%,#262626 100%);
  clip-path:polygon(0 0,1200px 0,1200px 642px,0 698px)}
.site-header{left:0;top:0;width:1200px;height:100px;border-bottom:1px solid rgba(255,255,255,.08)}
.brand{left:100px;top:28px;font-family:"Catamaran",sans-serif;font-weight:800;font-size:38px;letter-spacing:1px;color:var(--paper)}
.nav-link{top:38px;font-size:14px;font-weight:600;color:var(--paper);letter-spacing:.3px}
.nav-link.active{border-bottom:2px solid var(--paper);padding-bottom:6px}
.btn-login{left:841px;top:33px;width:79px;height:33px;border:1.5px solid var(--paper);color:var(--paper);font-size:14px;font-weight:600;display:flex;align-items:center;justify-content:center}
.btn-member{left:936px;top:33px;width:166px;height:33px;background:var(--paper);color:var(--ink);font-size:14px;font-weight:600;display:flex;align-items:center;justify-content:center}
.hero-title{top:270px;font-family:"Catamaran",sans-serif;font-weight:700;font-size:58px;color:var(--paper)}
.dot{top:607px;width:14px;height:14px;border-radius:50%;background:#9a9a9a}
.dot.on{background:var(--paper)}

/* headings */
.section-title{font-family:"Catamaran",sans-serif;font-weight:700;font-size:40px}
.rule{width:70px;height:3px;left:565px}
.body-copy{font-size:16.5px;line-height:23px}
.btn-apply{left:533px;width:134px;height:45px;background:var(--ink);color:var(--paper);font-size:20px;display:flex;align-items:center;justify-content:center;letter-spacing:.5px}

.subtitle{top:838px;font-family:"Encode Sans Condensed",sans-serif;font-weight:400;font-size:32px}

/* services */
.services{left:0;top:1212px;width:1200px;height:804px;
  background:radial-gradient(ellipse at 50% 40%,#2a2a2a 0%,#161616 55%,#0c0c0c 100%);
  clip-path:polygon(0 0,1200px 0,1200px 804px,0 750px)}
.service{width:260px;text-align:center;color:var(--paper)}
.service svg{display:block;margin:0 auto}
.service-label{margin-top:14px;font-size:14.5px;font-weight:600;letter-spacing:.2px}

/* footer */
.site-footer{left:0;top:2408px;width:1200px;height:486px;background:var(--dark);
  clip-path:polygon(0 46px,1200px 0,1200px 486px,0 486px)}
.crumbs{top:2473px;font-size:11px;color:var(--faint);word-spacing:2px}
.crumbs span{margin:0 14px}
.footer-note{top:2588px;font-size:16px;color:var(--muted)}
.btn-subscribe{left:528px;top:2633px;width:143px;height:47px;border:1.5px solid #cfcfcf;color:var(--paper);font-size:19px;display:flex;align-items:center;justify-content:center}
.social{top:2725px;width:36px;height:36px;border:1.5px solid #d0d0d0;border-radius:50%}
.footer-rule{left:100px;top:2803px;width:1000px;height:1px;background:var(--line)}
.copyright{top:2840px;font-size:13px;color:#d8d8d8}
</style>
</head>
<body>

<!-- hero -->
<div class="abs hero" role="img" aria-label="Black and white photo of a palm-lined beach with people walking on the sand"></div>
<header class="abs site-header">
  <div class="abs brand">VELMOR</div>
  <nav>
    <span class="abs nav-link active" style="left:380px">HOME</span>
    <span class="abs nav-link" style="left:463px">ABOUT</span>
    <span class="abs nav-link" style="left:550px">SERVICES AND BENEFITS</span>
    <span class="abs nav-link" style="left:745px">CONTACT</span>
    <span class="abs btn-login">LOG IN</span>
    <span class="abs btn-member">BECOME A MEMBER</span>
  </nav>
</header>
<h1 class="abs center hero-title">A Members Only Lifestyle Club</h1>
<span class="abs dot on" style="left:552px"></span>
<span class="abs dot" style="left:579px"></span>
<span class="abs dot" style="left:606px"></span>
<span class="abs dot" style="left:633px"></span>

<!-- about -->
<h2 class="abs center section-title" style="top:754px">About VELMOR</h2>
<div class="abs rule" style="top:814px;background:var(--ink)"></div>
<p class="abs center subtitle">The ultimate full service lifestyle club</p>
<p class="abs body-copy" style="left:150px;width:900px;top:901px;text-align:center">VELMOR was formed to bring the best services, experiences, and exclusive opportunities to our members. With everything from private member events to private jet travel, the perks of being a VELMOR member are unmatched. Professional athletes, artists, musicians, corporate professionals: Our members come from diverse backgrounds.</p>
<p class="abs center body-copy" style="top:996px">Comprehensive services like 24/7 concierge, accountants, attorneys, private advisers, planners, investment advisors and more.</p>
<div class="abs btn-apply" style="top:1073px">APPLY</div>

<!-- services -->
<section class="abs services" role="img" aria-label="Dark photo of two people jogging along a boardwalk"></section>
<h2 class="abs center section-title" style="top:1298px;color:var(--paper)">Services and Benefits</h2>
<div class="abs rule" style="top:1349px;background:var(--paper)"></div>

<div class="abs service" style="left:210px;top:1405px">
  <svg width="100" height="100" viewBox="0 0 100 100" fill="none" stroke="#fff" stroke-width="2"><circle cx="50" cy="50" r="49" stroke="#555"/><rect x="33" y="30" width="26" height="36" rx="2"/><path d="M38 40h16M38 47h10M38 54h12"/><path d="M54 66l14-20 4 3-14 20-5 2z"/></svg>
  <div class="service-label">ACCOUNTING SERVICES</div>
</div>
<div class="abs service" style="left:470px;top:1405px">
  <svg width="100" height="100" viewBox="0 0 100 100" fill="none" stroke="#fff" stroke-width="2"><circle cx="50" cy="50" r="49" stroke="#555"/><path d="M32 68h36M36 68V56h6v12M46 68V50h6v12M56 68V44h6v24"/><path d="M34 48l12-8 8 4 14-12M62 32h6v6"/></svg>
  <div class="service-label">INVESTMENT SERVICES</div>
</div>
<div class="abs service" style="left:727px;top:1405px">
  <svg width="100" height="100" viewBox="0 0 100 100" fill="none" stroke="#fff" stroke-width="2"><circle cx="50" cy="50" r="49" stroke="#555"/><path d="M50 30v38M40 68h20M32 38h36"/><path d="M32 38l-7 14h14zM68 38l-7 14h14z"/><circle cx="50" cy="30" r="2"/></svg>
  <div class="service-label">LAWYER SERVICES</div>
</div>

<div class="abs service" style="left:210px;top:1567px">
  <svg width="100" height="100" viewBox="0 0 100 100" fill="none" stroke="#fff" stroke-width="2"><circle cx="50" cy="50" r="49" stroke="#555"/><path d="M32 36h36v-6H32zM34 36v32h32V36"/><path d="M32 36q4 6 8 0q4 6 8 0q4 6 8 0q4 6 8 0q2 4 4 0"/><rect x="39" y="46" width="8" height="8"/><rect x="53" y="46" width="8" height="22"/></svg>
  <div class="service-label">REAL ESTATE SERVICES</div>
</div>
<div class="abs service" style="left:470px;top:1567px">
  <svg width="100" height="100" viewBox="0 0 100 100" fill="none" stroke="#fff" stroke-width="2"><circle cx="50" cy="50" r="49" stroke="#555"/><path d="M24 44l10-8 10 4 8-2 10 6 14-4M24 44l6 12 14 10 6-2 4 2 6-4 6-6 10-10"/><path d="M44 40l-6 8 4 2 8-6M46 58l4 4M50 54l6 6M54 50l6 6"/></svg>
  <div class="service-label">24/7 CONCIERGE</div>
</div>
<div class="abs service" style="left:727px;top:1567px">
  <svg width="100" height="100" viewBox="0 0 100 100" fill="none" stroke="#fff" stroke-width="2"><circle cx="50" cy="50" r="49" stroke="#555"/><path d="M66 30c4-2 6 0 4 4L58 48l4 18-3 3-8-14-9 9 1 6-3 2-3-7-7-3 2-3 6 1 9-9-14-8 3-3 18 4z"/></svg>
  <div class="service-label">PRIVATE JET TRAVEL</div>
</div>

<div class="abs service" style="left:210px;top:1729px">
  <svg width="100" height="100" viewBox="0 0 100 100" fill="none" stroke="#fff" stroke-width="2"><circle cx="50" cy="50" r="49" stroke="#555"/><rect x="32" y="34" width="36" height="34" rx="2"/><path d="M32 42h36M39 30v8M61 30v8M38 48h24M38 55h24M38 62h24M44 42v26M50 42v26M56 42v26"/></svg>
  <div class="service-label">EVENT ACCESS</div>
</div>
<div class="abs service" style="left:470px;top:1729px">
  <svg width="100" height="100" viewBox="0 0 100 100" fill="none" stroke="#fff" stroke-width="2"><circle cx="50" cy="50" r="49" stroke="#555"/><path d="M34 38l12 4-3 10q-5 3-9-1zM66 38l-12 4 3 10q5 3 9-1zM40 53l-5 14M60 53l5 14M30 68h10M60 68h10M50 26v6M42 30l3 4M58 30l-3 4"/></svg>
  <div class="service-label">PRIVATE EVENTS</div>
</div>
<div class="abs service" style="left:727px;top:1729px">
  <svg width="100" height="100" viewBox="0 0 100 100" fill="none" stroke="#fff" stroke-width="2"><circle cx="50" cy="50" r="49" stroke="#555"/><rect x="30" y="38" width="40" height="28" rx="3"/><path d="M43 38v-5h14v5M30 50h40M47 47h6v6h-6z"/></svg>
  <div class="service-label">EXPERIENCES</div>
</div>

<!-- we are -->
<h2 class="abs center section-title" style="top:2062px">We Are VELMOR</h2>
<div class="abs rule" style="top:2122px;background:var(--ink)"></div>
<p class="abs body-copy" style="left:240px;width:720px;top:2149px;text-align:center">Built in the image of a"Multi-Family Office", VELMOR provides members with access to just about any service, experience, and event desirable.</p>
<p class="abs center body-copy" style="top:2218px">VELMOR is truly the most exclusive lifestyle club out there.</p>
<div class="abs btn-apply" style="top:2289px">APPLY</div>

<!-- footer -->
<footer class="abs site-footer"></footer>
<nav class="abs center crumbs"><span>Home</span>·<span>About</span>·<span>Services and Benefits</span>·<span>Contact</span></nav>
<h2 class="abs center section-title" style="top:2522px;color:var(--paper)">Contact Us</h2>
<div class="abs rule" style="top:2572px;background:var(--paper)"></div>
<p class="abs center footer-note">sign up with your email address to receive news and updates.</p>
<div class="abs btn-subscribe">SUBSCRIBE</div>
<span class="abs social" style="left:499px" aria-label="Social link"></span>
<span class="abs social" style="left:540px" aria-label="Social link"></span>
<span class="abs social" style="left:580px" aria-label="Social link"></span>
<span class="abs social" style="left:621px" aria-label="Social link"></span>
<span class="abs social" style="left:663px" aria-label="Social link"></span>
<div class="abs footer-rule"></div>
<p class="abs center copyright">© 2018 VELMOR . All rights reserved.</p>

</body>
</html>
```